Northmead Career Institute needs a unique tri-fold brochure design

I need a tri-fold brochure for my vocational school. We provide Nursing Assistant, Home Healthcare Aide & Phlebotomy classes at our centers and 50 programs online. The theme for our brochure and logo is Opening New Doors. I have all the text for the brochure and simples of brochures that I Like. I want the brochure to stand out and represent high quality and success. I also want the brochure to be easy to read. Yes, I'm also open to different ideas and concepts. lol
Updates

The logo and a sample of the text are now available with my brief.

Thanks,

Rob

Thanks to all the designers who took on the project and emailed me directly! If you have not replied to the invite, email me at, rkestwin47@mailnova.test

Thanks again, 
Rob 

Hello All,

Payment for the project is now GUARANTEED! Feel free to email me directly at rkestwin47@mailnova.test or you can post your first draft on my page. Fyi... full content for the brochure is only available upon request.

Thanks,

Rob

Target Market(s)

18-55 years old, but the vast majority are between the age of 24-45

Industry/Entity Type

School

Requirements
Must have
• Pictures of people in scrubs of all ages.
Should not have
• pictures of people in business wear.

```html
<!DOCTYPE html>
<html lang="en">
<head>
<meta charset="utf-8">
<title>Northmead Career Institute – Tri-fold Brochure</title>
<link rel="stylesheet" href="https://fonts.googleapis.com/css2?family=Didact+Gothic&family=Questrial&display=swap">
<style>
  :root {
    --stage: #e8ebf3;
    --paper-top: #ffffff;
    --paper-bottom: #dff1fa;
    --wave-deep: #1aa3dc;
    --wave-mid: #5cc4ec;
    --wave-light: #aee2f7;
    --brand-navy: #1d3f8f;
    --accent-red: #d8232a;
    --ink: #2a2a2a;
    --tick-green: #2e9b3a;
    --list-blue: #1d5fb0;
    --photo-grad-a: #c9a98b;
    --photo-grad-b: #7c9fc4;
  }
  * { box-sizing: border-box; margin: 0; padding: 0; }
  html, body { width: 1200px; height: 876px; overflow: hidden; }
  body {
    background: var(--stage);
    font-family: "Didact Gothic", "Questrial", sans-serif;
    color: var(--ink);
  }
  .brochure {
    position: absolute;
    left: 60px; top: 21px;
    width: 1080px; height: 834px;
    display: flex;
    box-shadow: 0 10px 30px rgba(40, 60, 110, 0.25);
  }
  .panel {
    position: relative;
    width: 360px; height: 834px;
    background: linear-gradient(180deg, var(--paper-top) 0%, var(--paper-bottom) 100%);
    overflow: hidden;
  }
  .panel + .panel { border-left: 1px solid rgba(120, 160, 200, 0.25); }
  .wave { position: absolute; left: 0; width: 360px; }
  .wave--top { top: 0; height: 110px; }
  .wave--bottom { bottom: 0; height: 170px; }
  .panel__body { position: relative; z-index: 1; padding: 0 34px; }

  /* Testimonials */
  .testimonials .panel__body { padding-top: 70px; }
  .section-title {
    color: var(--accent-red);
    font-size: 17px;
    font-weight: 700;
    letter-spacing: 0.5px;
  }
  .section-sub {
    font-size: 16px;
    font-weight: 700;
    line-height: 1.2;
    margin-top: 2px;
  }
  .photo-frame {
    margin: 18px 0 0;
    border: 6px solid var(--wave-deep);
    border-radius: 16px;
    height: 170px;
    background: linear-gradient(160deg, #9fd0ef 0%, #3c4b5e 55%, #1d2530 100%);
  }
  .quote {
    font-size: 11.5px;
    line-height: 1.55;
    margin-top: 26px;
  }
  .quote__author {
    text-align: right;
    font-weight: 700;
    font-style: italic;
    font-size: 12px;
    margin-top: 4px;
  }
  .quote--second { margin-top: 40px; }

  /* Contact */
  .contact .panel__body { padding-top: 60px; text-align: center; }
  .intro { font-size: 11.5px; line-height: 1.55; }
  .intro + .intro { margin-top: 16px; }
  .contact-title {
    color: var(--accent-red);
    font-size: 18px;
    font-weight: 700;
    margin-top: 16px;
    letter-spacing: 0.5px;
  }
  .info-block { font-size: 11.5px; line-height: 1.5; margin-top: 12px; }
  .info-block h3 { font-size: 12px; font-weight: 700; }

  /* Cover */
  .cover .panel__body { padding-top: 70px; text-align: center; }
  .brand {
    display: flex; align-items: center; justify-content: center; gap: 8px;
    color: var(--brand-navy);
    font-size: 15px;
    font-weight: 700;
  }
  .brand__mark { width: 16px; height: 16px; border-radius: 50%; background: var(--brand-navy); }
  .headline {
    margin-top: 16px;
    line-height: 1;
  }
  .headline__main { display: block; color: var(--accent-red); font-size: 44px; }
  .headline__sub { display: block; color: var(--brand-navy); font-size: 26px; margin-top: 2px; }
  .benefits { list-style: none; margin-top: 20px; text-align: left; padding-left: 6px; }
  .benefits li {
    display: flex; align-items: center; gap: 6px;
    color: var(--list-blue);
    font-size: 12px;
    font-weight: 700;
    line-height: 1.9;
  }
  .benefits svg { flex: none; width: 11px; height: 11px; }
  .team-photo {
    position: absolute; z-index: 1;
    left: 20px; right: 10px; top: 430px; height: 250px;
    border-radius: 8px;
    background: linear-gradient(180deg, var(--photo-grad-b) 0%, #e8d6c8 45%, var(--photo-grad-a) 75%, #cf6f98 100%);
  }
  .enroll {
    position: absolute; z-index: 2;
    left: 0; right: 0; bottom: 46px;
    text-align: center;
    color: #fff;
    font-size: 14px;
    line-height: 1.35;
  }
  .enroll strong { font-size: 18px; font-weight: 400; }
</style>
</head>
<body>
  <main class="brochure">

    <section class="panel testimonials">
      <svg class="wave wave--top" viewBox="0 0 360 110" preserveAspectRatio="none" aria-hidden="true">
        <path d="M0 0 H360 V30 C260 70 120 20 0 55 Z" fill="var(--wave-light)"/>
        <path d="M0 0 H360 V14 C250 46 110 6 0 32 Z" fill="var(--wave-mid)"/>
      </svg>
      <svg class="wave wave--bottom" viewBox="0 0 360 170" preserveAspectRatio="none" aria-hidden="true">
        <path d="M0 60 C120 20 240 110 360 50 V170 H0 Z" fill="var(--wave-light)"/>
        <path d="M0 110 C130 70 250 150 360 100 V170 H0 Z" fill="var(--wave-mid)"/>
      </svg>
      <div class="panel__body">
        <h2 class="section-title">TESTIMONIALS</h2>
        <p class="section-sub">HERE'S WHAT OUR STUDENTS HAVE TO SAY ABOUT OUR CLASSES…</p>
        <div class="photo-frame" role="img" aria-label="Photo of smiling graduates in caps and gowns raising their arms outdoors"></div>
        <p class="quote">I inquired information from 3 different training centers before I became a HHA/CNA. The private schools wanted to charge $1000 to $1200 and told me I couldn't find a job if I did a prep course or challenge the CNA state exam. Well, I took the prep class at NCI and I passed my exam on the 1st try and I'm now working over 40 hours a week. The instructors were extremely knowledgeable, patient and willing to help. The staff were always there when needed and was very encouraging. I urge anyone to attend this training.</p>
        <p class="quote__author">Andre M. Lakeview FL</p>
        <p class="quote quote--second">My name is Tessa, for my CNA training I went to Northmead Career Institute. My teacher was wonderful, it was amazing. I passed my CNA state exam, with no problems. I now work with a client who is paralyzed from the waist down 4 days a week, and am currently looking for another part-time job in elderly care. My training was wonderful! Thanks NCI :-)</p>
        <p class="quote__author">Tessa R. Harbor Point, FL</p>
      </div>
    </section>

    <section class="panel contact">
      <svg class="wave wave--top" viewBox="0 0 360 110" preserveAspectRatio="none" aria-hidden="true">
        <path d="M0 0 H360 V24 C240 60 120 10 0 40 Z" fill="var(--wave-light)"/>
      </svg>
      <svg class="wave wave--bottom" viewBox="0 0 360 170" preserveAspectRatio="none" aria-hidden="true">
        <path d="M0 50 C120 110 240 20 360 70 V170 H0 Z" fill="var(--wave-light)"/>
        <path d="M0 100 C120 150 250 70 360 115 V170 H0 Z" fill="var(--wave-mid)"/>
      </svg>
      <div class="panel__body">
        <p class="intro">Enroll at the School that completely disregards the limitations and applies fresh and innovative methods and techniques to help you get the best of both worlds.</p>
        <p class="intro">We are the bridge to quickly reenter the workforce for displaced workers and for individuals looking for fulfilling and rewarding long-term employment while pursuing higher education.</p>
        <h2 class="contact-title">HOW TO CONTACT US</h2>
        <div class="info-block">
          <h3>Operation Hours:</h3>
          <p>Monday through Thursday – 9am to 5pm</p>
          <p>Friday- 9am to 3pm</p>
          <p>Saturday- By appointment only</p>
        </div>
        <div class="info-block">
          <h3>Harbor Point Center</h3>
          <p>1450 Marlow Avenue</p>
          <p>Unit 201-203</p>
          <p>Harbor Point, Florida 30001</p>
          <p>Tel: (555) 014-0717</p>
          <p>Fax: 555-019-1180</p>
        </div>
        <div class="info-block">
          <h3>Westbrook/Palm Shore Center</h3>
          <p>7800 Palm Shore Road</p>
          <p>Palm Shore, FL 30002</p>
          <p>Tel: (555) 016-9209</p>
          <p>Fax: 555-019-1180</p>
          <p>BY APPOINTMENT ONLY</p>
        </div>
        <div class="info-block">
          <h3>Department Contact Information</h3>
          <p>Sign up: 555-014-0717 ext 101</p>
          <p>Customer Service: 555-014-0717 ext 102</p>
          <p>Online Store: 555-014-0717 ext 103</p>
        </div>
      </div>
    </section>

    <section class="panel cover">
      <svg class="wave wave--top" viewBox="0 0 360 110" preserveAspectRatio="none" aria-hidden="true">
        <path d="M0 0 H360 V60 C250 20 120 70 0 30 Z" fill="var(--wave-light)"/>
        <path d="M0 0 H360 V36 C240 4 120 46 0 14 Z" fill="var(--wave-mid)"/>
      </svg>
      <svg class="wave wave--bottom" viewBox="0 0 360 170" preserveAspectRatio="none" aria-hidden="true">
        <path d="M0 40 C120 0 240 60 360 20 V170 H0 Z" fill="var(--wave-light)"/>
        <path d="M0 70 C130 30 250 90 360 45 V170 H0 Z" fill="var(--wave-deep)"/>
      </svg>
      <div class="panel__body">
        <div class="brand"><span class="brand__mark" aria-hidden="true"></span>Northmead Career Institute</div>
        <h1 class="headline">
          <span class="headline__main">Opening</span>
          <span class="headline__sub">New Doors</span>
        </h1>
        <ul class="benefits">
          <li><svg viewBox="0 0 12 12" aria-hidden="true"><path d="M1 6.5 L4.5 10 L11 2" fill="none" stroke="var(--tick-green)" stroke-width="2"/></svg>Affordable &amp; Quality Education</li>
          <li><svg viewBox="0 0 12 12" aria-hidden="true"><path d="M1 6.5 L4.5 10 L11 2" fill="none" stroke="var(--tick-green)" stroke-width="2"/></svg>Fast &amp; Efficient Training</li>
          <li><svg viewBox="0 0 12 12" aria-hidden="true"><path d="M1 6.5 L4.5 10 L11 2" fill="none" stroke="var(--tick-green)" stroke-width="2"/></svg>High Paying Jobs &amp; Rewarding Careers</li>
          <li><svg viewBox="0 0 12 12" aria-hidden="true"><path d="M1 6.5 L4.5 10 L11 2" fill="none" stroke="var(--tick-green)" stroke-width="2"/></svg>State Certified Caregivers &amp; Highly Rated Employees</li>
          <li><svg viewBox="0 0 12 12" aria-hidden="true"><path d="M1 6.5 L4.5 10 L11 2" fill="none" stroke="var(--tick-green)" stroke-width="2"/></svg>Training Facility &amp; Community</li>
        </ul>
      </div>
      <div class="team-photo" role="img" aria-label="Group photo of smiling healthcare workers of different ages in scrubs and white coats"></div>
      <p class="enroll">Enroll Online:<br>northmeadcareer.test<br>Or Call: <strong>555-014-0717</strong></p>
    </section>

  </main>
</body>
</html>
```